Business Card for a New Zealand IT Startup

I need a business card for VELTA Holdings. We are a young startup based in New Zealand working in internet marketing and web development. The design should have some element connected to New Zealand, such as wave, koru or silver fern, just don't use a kiwi bird.

```html
<!DOCTYPE html>
<html lang="en">
<head>
<meta charset="utf-8">
<title>VELTA Holdings – Business Card</title>
<link rel="stylesheet" href="https://fonts.googleapis.com/css2?family=Roboto:wght@400;500;700&display=swap">
<style>
  :root {
    --page: #ecebe8;
    --card-white: #ffffff;
    --brand-blue: #0070bb;
    --brand-orange: #f15a24;
    --ink-white: #ffffff;
    --shadow: rgba(0, 0, 0, 0.28);
  }
  * { margin: 0; padding: 0; box-sizing: border-box; }
  html, body {
    width: 1125px; height: 1200px; overflow: hidden;
    background: var(--page);
    font-family: "Roboto", Arial, sans-serif;
  }
  .sheet { position: relative; width: 1125px; height: 1200px; }
  .card {
    position: absolute; left: 150px; width: 825px; height: 470px;
    border-radius: 26px; overflow: hidden;
    box-shadow: 0 4px 10px var(--shadow);
  }
  .card-front { top: 105px; background: var(--card-white); }
  .card-back { top: 640px; background: var(--brand-blue); }
  .front-wave { position: absolute; inset: 0; width: 825px; height: 470px; }

  .wordmark {
    position: absolute; left: 42px; top: 60px;
    display: flex; align-items: center; gap: 14px;
  }
  .wordmark-name {
    font-weight: 700; font-size: 44px; letter-spacing: 1px;
    color: var(--brand-blue); line-height: 1;
  }
  .wordmark-dot {
    width: 30px; height: 30px; border-radius: 50%;
    background: var(--brand-blue);
  }

  .contact-block {
    position: absolute; right: 46px; top: 160px;
    text-align: right; color: var(--ink-white);
  }
  .person-name { font-size: 29px; font-weight: 500; letter-spacing: 0.5px; line-height: 1.1; }
  .person-role { font-size: 20px; font-weight: 500; margin-top: 2px; }
  .address { font-size: 19px; line-height: 25px; margin-top: 16px; }
  .contact-list { list-style: none; margin-top: 12px; }
  .contact-list li {
    display: flex; justify-content: flex-end; align-items: center;
    gap: 9px; font-size: 18.5px; line-height: 26px;
  }
  .contact-list svg { width: 18px; height: 18px; flex: none; }

  .back-name {
    position: absolute; left: 0; right: 0; top: 180px;
    display: flex; justify-content: center; align-items: center; gap: 16px;
  }
  .back-name-text {
    font-weight: 700; font-size: 52px; letter-spacing: 1px;
    color: var(--ink-white); line-height: 1;
  }
  .back-name-dot {
    width: 36px; height: 36px; border-radius: 50%; background: var(--ink-white);
  }
  .back-web {
    position: absolute; left: 0; right: 0; top: 390px;
    text-align: center; color: var(--ink-white);
    font-size: 20px; letter-spacing: 6px;
  }
  .back-web strong { font-weight: 500; }
</style>
</head>
<body>
<main class="sheet">

  <section class="card card-front" aria-label="Card front">
    <svg class="front-wave" viewBox="0 0 825 470" aria-hidden="true">
      <path class="wave-thin" fill="var(--brand-orange)"
        d="M20 440 C150 455 290 400 385 295 C455 190 520 115 620 92 C680 80 740 80 790 95
           C740 90 690 92 630 103 C530 125 470 195 395 305 C300 415 160 455 20 440 Z"/>
      <path class="wave-gap" fill="var(--card-white)" transform="translate(0 -12)"
        d="M0 400 C130 470 300 430 400 320 C470 210 530 140 630 115 C720 95 790 125 825 155 L825 490 L0 490 Z"/>
      <path class="wave-main" fill="var(--brand-orange)"
        d="M0 400 C130 470 300 430 400 320 C470 210 530 140 630 115 C720 95 790 125 825 155 L825 470 L0 470 Z"/>
    </svg>

    <div class="wordmark">
      <span class="wordmark-name">VELTA HOLDINGS</span>
      <span class="wordmark-dot"></span>
    </div>

    <div class="contact-block">
      <p class="person-name">MARA QUINLAN</p>
      <p class="person-role">CEO/FOUNDER</p>
      <p class="address">214 Harbour View Road<br>Wellington, New Zealand 6011</p>
      <ul class="contact-list">
        <li>021 555 0147
          <svg viewBox="0 0 24 24"><path fill="#fff" d="M6.6 10.8a15.1 15.1 0 0 0 6.6 6.6l2.2-2.2a1 1 0 0 1 1-.25 11.4 11.4 0 0 0 3.6.57 1 1 0 0 1 1 1V20a1 1 0 0 1-1 1A17 17 0 0 1 3 4a1 1 0 0 1 1-1h3.5a1 1 0 0 1 1 1c0 1.25.2 2.45.57 3.57a1 1 0 0 1-.25 1z"/></svg>
        </li>
        <li>022 555 0283
          <svg viewBox="0 0 24 24"><rect x="6" y="2" width="12" height="20" rx="2" fill="none" stroke="#fff" stroke-width="2"/><circle cx="12" cy="18.5" r="1.2" fill="#fff"/></svg>
        </li>
        <li>04 555 0396
          <svg viewBox="0 0 24 24"><rect x="7" y="3" width="10" height="7" fill="#fff"/><rect x="3" y="10" width="18" height="9" rx="2" fill="#fff"/><rect x="7" y="15" width="10" height="6" fill="var(--brand-orange)" stroke="#fff" stroke-width="1.5"/></svg>
        </li>
        <li>mara@veltaholdings.com
          <svg viewBox="0 0 24 24"><rect x="3" y="6" width="18" height="13" fill="#fff"/><path d="M3 6l9 7 9-7" fill="none" stroke="var(--brand-orange)" stroke-width="1.6"/></svg>
        </li>
        <li>www.veltaholdings.com
          <svg viewBox="0 0 24 24"><circle cx="12" cy="12" r="9" fill="#fff"/><path d="M8 7c2 1 1 3 3 4s0 3-1 4M15 6c-1 2 1 3 2 5" fill="none" stroke="var(--brand-orange)" stroke-width="1.6"/></svg>
        </li>
      </ul>
    </div>
  </section>

  <section class="card card-back" aria-label="Card back">
    <div class="back-name">
      <span class="back-name-text">VELTA HOLDINGS</span>
      <span class="back-name-dot"></span>
    </div>
    <p class="back-web">www.<strong>veltaholdings</strong>.com</p>
  </section>

</main>
</body>
</html>
```